IT Consulting Business Card Design

We need a business card on our company name....which is a IT consulting and staffing company. We also train masters graduates in various IT courses. 70% of the time these cards will be handed out to the graduate students at the universities. 30% for our clients and business partners. We are uploading our company logo...would like to see something that matches our logo or blends with it. Please visit www.brightpinesolutions.com for more details on logo and colors.

Target Market(s)

70% of the time these cards will be handed out to the graduate students at the universities. 30% for our clients and business partners.

Industry/Entity Type

Business

Contact Information for Business Card

Reno Valcourt
Vice-President
Bright Pine Works Inc
3187 Mercer Lane, Suite 412
Alder Falls, NJ 08214
reno@brightpinesolutions.com
Office : 1-855-290-1837 X 614
Cell number : 908-731-2094

Requirements
Nice to have
• may be company logo and name on the back of the card and detials on the other side...just a thought..!!

```html
<!DOCTYPE html>
<html lang="en">
<head>
<meta charset="utf-8">
<title>Bright Pine Works – Business Card</title>
<link rel="stylesheet" href="https://fonts.googleapis.com/css2?family=Open+Sans:wght@400;600;700&display=swap">
<style>
  :root {
    --bg: #3a3a3a;
    --card-black: #0e0e0e;
    --card-black-soft: #2a2a2a;
    --card-white: #ffffff;
    --brand-red: #d8202a;
    --brand-red-dark: #a3121b;
    --swoosh-grey: #4a4a4a;
    --ink: #3b3b3b;
    --text-light: #ffffff;
    --text-muted: #c9c9c9;
  }
  * { box-sizing: border-box; margin: 0; padding: 0; }
  html, body { width: 1200px; height: 716px; overflow: hidden; }
  body {
    background: var(--bg);
    font-family: "Open Sans", Arial, sans-serif;
    position: relative;
  }
  .card {
    position: absolute;
    top: 208px;
    width: 525px;
    height: 300px;
    border-radius: 22px;
    overflow: hidden;
  }
  /* Back of card */
  .card-back {
    left: 50px;
    background: radial-gradient(ellipse at 40% 35%, var(--card-black-soft), var(--card-black) 70%);
  }
  .card-back .texture {
    position: absolute;
    left: 60px; top: -20px;
    width: 360px; height: 300px;
    border-radius: 50%;
    background: radial-gradient(circle at 50% 40%, rgba(255,255,255,0.10), rgba(255,255,255,0) 65%);
  }
  .logo {
    position: absolute;
    display: flex;
    align-items: center;
    gap: 12px;
  }
  .logo-dot {
    width: 46px; height: 46px;
    border-radius: 50%;
    background: var(--brand-red);
    flex: none;
  }
  .logo-name {
    font-weight: 700;
    font-size: 24px;
    letter-spacing: 0.5px;
    white-space: nowrap;
  }
  .card-back .logo { left: 100px; top: 105px; }
  .card-back .logo-name { color: var(--text-light); }
  .card-back .web {
    position: absolute;
    left: 150px; top: 172px;
    color: var(--text-muted);
    font-size: 12px;
  }
  /* Front of card */
  .card-front {
    left: 625px;
    background: var(--card-white);
  }
  .card-front .wave { position: absolute; inset: 0; }
  .card-front .logo { left: 120px; top: 50px; }
  .card-front .logo-name { color: var(--ink); }
  .contact {
    position: absolute;
    left: 32px; top: 150px;
    color: var(--text-light);
    font-size: 11.5px;
    line-height: 1.45;
  }
  .contact .name { font-size: 13px; letter-spacing: 0.5px; text-transform: uppercase; }
  .contact .role { margin-bottom: 6px; }
  .contact-line { display: flex; align-items: center; gap: 6px; }
  .contact-line svg { width: 10px; height: 10px; flex: none; }
  .address {
    position: absolute;
    right: 28px; bottom: 22px;
    text-align: right;
    color: var(--text-light);
    font-size: 12px;
    font-style: normal;
    line-height: 1.45;
  }
</style>
</head>
<body>

<section class="card card-back" aria-label="Card back">
  <div class="texture" role="img" aria-label="Soft dotted sphere texture"></div>
  <div class="logo">
    <span class="logo-dot"></span>
    <span class="logo-name">BRIGHT PINE WORKS</span>
  </div>
  <p class="web">www.brightpinesolutions.com</p>
</section>

<section class="card card-front" aria-label="Card front">
  <svg class="wave" viewBox="0 0 525 300" preserveAspectRatio="none" aria-hidden="true">
    <defs>
      <linearGradient id="redFill" x1="0" y1="0" x2="1" y2="1">
        <stop offset="0" stop-color="#e1252f"/>
        <stop offset="1" stop-color="#a3121b"/>
      </linearGradient>
    </defs>
    <path d="M0 128 C120 100 210 150 300 175 C390 200 460 170 525 130 L525 146 C460 190 390 215 300 190 C210 165 120 118 0 142 Z" fill="var(--swoosh-grey)"/>
    <path d="M0 142 C120 118 210 165 300 190 C390 215 460 190 525 146 L525 300 L0 300 Z" fill="url(#redFill)"/>
  </svg>
  <div class="logo">
    <span class="logo-dot"></span>
    <span class="logo-name">BRIGHT PINE WORKS</span>
  </div>
  <div class="contact">
    <p class="name">Reno Valcourt</p>
    <p class="role">Vice-President</p>
    <p class="contact-line">
      <svg viewBox="0 0 10 10"><path d="M2 1 L4 1 L4.6 3 L3.4 3.8 C4 5 5 6 6.2 6.6 L7 5.4 L9 6 L9 8 C5 8.5 1.5 5 2 1 Z" fill="#fff"/></svg>
      1-855-290-1837 X 614
    </p>
    <p class="contact-line">
      <svg viewBox="0 0 10 10"><rect x="2.5" y="0.5" width="5" height="9" rx="1" fill="#fff"/><rect x="3.3" y="1.6" width="3.4" height="5.6" fill="#c01a23"/></svg>
      908-731-2094
    </p>
    <p class="contact-line">
      <svg viewBox="0 0 10 10"><rect x="0.5" y="2" width="9" height="6" fill="#fff"/><path d="M0.5 2 L5 5.5 L9.5 2" stroke="#c01a23" fill="none"/></svg>
      reno@brightpinesolutions.com
    </p>
    <p class="contact-line">
      <svg viewBox="0 0 10 10"><circle cx="5" cy="5" r="4.3" fill="none" stroke="#fff"/><path d="M0.7 5 H9.3 M5 0.7 C3 3 3 7 5 9.3 M5 0.7 C7 3 7 7 5 9.3" stroke="#fff" fill="none" stroke-width="0.7"/></svg>
      www.brightpinesolutions.com
    </p>
  </div>
  <address class="address">
    Bright Pine Works Inc<br>
    3187 Mercer Lane,<br>
    Suite 412 Alder Falls, NJ 08214
  </address>
</section>

</body>
</html>
```